Corporate Design für logopädische Praxis
Zielgruppe
Ich gründe eine logopädische Praxis, die Sprachtherapie sowohl für Erwachsene als auch Kinder anbietet und damit ein Logo benötigt, das jede Altersgruppe anspricht und 'Lindenhof' als fachliche und menschliche Qualitätszeit interpretiert.
Aufgabenstellung
Ich bevorzuge ein klares Design, welches das Wortspiel der 'Lindenhof' im Idealfall aufgreift und den Patienten vermittelt, dass sowohl die fachliche Qualität der Behandlung als auch die Ebene von Empathie und Patientenorientierung im zwischenmenschlichen Umgang für die Praxis zentral sind.

```html
<!DOCTYPE html>
<html lang="de">
<head>
<meta charset="utf-8">
<title>Lindenhof – Praxis für Logopädie · Geschäftsausstattung</title>
<link href="https://fonts.googleapis.com/css2?family=Montserrat:wght@300;400&display=swap" rel="stylesheet">
<style>
  :root {
    --lavender: #adafd6;
    --lilac: #cdb9dc;
    --paper: #fafafc;
    --paper-footer: #f3f3f8;
    --ink: #8a8a92;
    --ink-soft: #a5a5ad;
    --backdrop: #ffffff;
    --shadow: 0 3px 8px rgba(0,0,0,.22);
  }
  * { box-sizing: border-box; margin: 0; padding: 0; }
  html, body { width: 1107px; height: 1200px; overflow: hidden; background: var(--backdrop); }
  body { position: relative; font-family: "Montserrat", sans-serif; font-weight: 300; color: var(--ink); }

  .sheet { position: absolute; background: var(--paper); box-shadow: var(--shadow); overflow: hidden; }
  .stripe { position: absolute; left: 0; right: 0; top: 0; background: var(--lilac); }

  .brand { display: flex; flex-direction: column; align-items: center; color: #fff; text-align: center; }
  .brand-dot { border-radius: 50%; border: 2px solid currentColor; }
  .brand-name { font-weight: 400; letter-spacing: .02em; line-height: 1; }
  .brand-tag { font-weight: 300; letter-spacing: .08em; text-transform: uppercase; white-space: nowrap; }

  .tiny { font-size: 4.6px; letter-spacing: .12em; line-height: 1.25; white-space: nowrap; }

  /* Header close-up */
  .header-detail { left: 33px; top: 33px; width: 1039px; height: 403px; }
  .header-detail .stripe { height: 12px; }
  .header-detail .logo-box { position: absolute; left: 300px; top: 12px; width: 240px; height: 230px; background: var(--lavender); justify-content: center; gap: 10px; }
  .header-detail .brand-dot { width: 34px; height: 34px; }
  .header-detail .brand-name { font-size: 34px; }
  .header-detail .brand-tag { font-size: 10px; }
  .header-detail .sender { position: absolute; left: 60px; top: 330px; font-size: 11px; letter-spacing: .14em; line-height: 1.35; }
  .header-detail .contact { position: absolute; left: 700px; top: 190px; font-size: 11px; letter-spacing: .14em; line-height: 1.4; }
  .contact-grid { display: grid; grid-template-columns: 90px auto; margin: 12px 0; }

  /* Letterhead */
  .letterhead { left: 56px; top: 491px; width: 466px; height: 657px; }
  .letterhead .stripe { height: 5px; }
  .letterhead .logo-box { position: absolute; left: 191px; top: 5px; width: 85px; height: 82px; background: var(--lavender); justify-content: center; gap: 4px; }
  .letterhead .brand-dot { width: 12px; height: 12px; border-width: 1px; }
  .letterhead .brand-name { font-size: 12px; }
  .letterhead .brand-tag { font-size: 3.8px; }
  .letterhead .sender { position: absolute; left: 53px; top: 121px; }
  .letterhead .contact { position: absolute; left: 349px; top: 121px; }
  .letterhead .contact-grid { grid-template-columns: 43px auto; margin: 5px 0; }
  .fold-mark { position: absolute; left: 0; width: 18px; height: 1px; background: #c9c9d0; }
  .letterhead .footer { position: absolute; left: 0; right: 0; bottom: 0; height: 97px; background: var(--paper-footer); }
  .footer-col { position: absolute; top: 53px; height: 32px; border-left: 1px solid #9a9aa3; padding-left: 6px; padding-top: 2px; }

  /* Envelopes */
  .envelope-back { left: 561px; top: 491px; width: 489px; height: 244px; }
  .envelope-back .flap { position: absolute; left: 0; top: 0; width: 489px; height: 70px; }
  .envelope-front { left: 561px; top: 752px; width: 489px; height: 244px; }
  .envelope-front .stripe { height: 5px; }
  .envelope-front .brand { position: absolute; left: 95px; top: 32px; width: 110px; color: var(--lavender); gap: 5px; }
  .envelope-front .brand-dot { width: 15px; height: 15px; border-width: 1.5px; }
  .envelope-front .brand-name { font-size: 17px; }
  .envelope-front .brand-tag { font-size: 6px; }
  .window { position: absolute; left: 45px; top: 112px; width: 199px; height: 100px; border-radius: 8px; background: linear-gradient(#f4f4f7, #ebebef); box-shadow: inset 0 0 6px rgba(0,0,0,.12); padding: 18px 19px; }

  /* Business cards */
  .card-front { left: 561px; top: 1024px; width: 189px; height: 122px; background: var(--lavender); justify-content: center; gap: 7px; display: flex; }
  .card-front .brand-dot { width: 22px; height: 22px; }
  .card-front .brand-name { font-size: 22px; }
  .card-front .brand-tag { font-size: 7px; }
  .card-back { left: 783px; top: 1024px; width: 189px; height: 122px; }
  .card-back .stripe { height: 7px; }
</style>
</head>
<body>

  <section class="sheet header-detail" aria-label="Briefkopf im Detail">
    <div class="stripe"></div>
    <div class="brand logo-box">
      <span class="brand-dot"></span>
      <span class="brand-name">Lindenhof</span>
      <span class="brand-tag">Praxis für Logopädie</span>
    </div>
    <p class="sender">LINDENHOF<br>Ihre Straße 30 &nbsp;|&nbsp; 60325 Ihre Stadt</p>
    <div class="contact">
      <p>LINDENHOF<br>Ihre Straße 30<br>60325 Ihre Stadt</p>
      <div class="contact-grid">
        <span>Telefon</span><span>069 5512 3380</span>
        <span>Telefax</span><span>069 5512 3381</span>
        <span>Mobil</span><span>0151 48260937</span>
      </div>
      <p>info@lindenhof-praxis.de</p>
    </div>
  </section>

  <section class="sheet letterhead" aria-label="Briefbogen">
    <div class="stripe"></div>
    <div class="brand logo-box">
      <span class="brand-dot"></span>
      <span class="brand-name">Lindenhof</span>
      <span class="brand-tag">Praxis für Logopädie</span>
    </div>
    <p class="tiny sender">LINDENHOF<br>Ihre Straße 30 &nbsp;|&nbsp; 60325 Ihre Stadt</p>
    <div class="tiny contact">
      <p>LINDENHOF<br>Ihre Straße 30<br>60325 Ihre Stadt</p>
      <div class="contact-grid">
        <span>Telefon</span><span>069 5512 3380</span>
        <span>Telefax</span><span>069 5512 3381</span>
        <span>Mobil</span><span>0151 48260937</span>
      </div>
      <p>info@lindenhof-praxis.de</p>
    </div>
    <span class="fold-mark" style="top:222px"></span>
    <span class="fold-mark" style="top:329px"></span>
    <span class="fold-mark" style="top:443px"></span>
    <div class="footer">
      <p class="tiny footer-col" style="left:61px">LINDENHOF<br>vertreten durch Marlene Voss<br>Ihre Straße 30<br>60325 Ihre Stadt</p>
      <p class="tiny footer-col" style="left:212px">Steuernummer 045 311 20584<br>Handelsregister HRB 204417<br>Registergericht Ihre Stadt<br>Ust. IdNr. DE208553146</p>
    </div>
  </section>

  <section class="sheet envelope-back" aria-label="Briefumschlag Rückseite">
    <svg class="flap" viewBox="0 0 489 70" aria-hidden="true">
      <path d="M0 0 H489 L481 56 Q479 69 466 69 H23 Q10 69 8 56 Z" fill="var(--lavender)"/>
    </svg>
  </section>

  <section class="sheet envelope-front" aria-label="Briefumschlag Vorderseite">
    <div class="stripe"></div>
    <div class="brand">
      <span class="brand-dot"></span>
      <span class="brand-name">Lindenhof</span>
      <span class="brand-tag">Praxis für Logopädie</span>
    </div>
    <div class="window">
      <p class="tiny">LINDENHOF<br>Ihre Straße 30 &nbsp;|&nbsp; 60325 Ihre Stadt</p>
    </div>
  </section>

  <section class="sheet brand card-front" aria-label="Visitenkarte Vorderseite">
    <span class="brand-dot"></span>
    <span class="brand-name">Lindenhof</span>
    <span class="brand-tag">Praxis für Logopädie</span>
  </section>

  <section class="sheet card-back" aria-label="Visitenkarte Rückseite">
    <div class="stripe"></div>
  </section>

</body>
</html>
```